The most modern business card ever !!!

Our company call “Vendalo”. Vendalo is a technology company specialized in cruises solutions. Out main product is a platform to reserve cruises. This is a revolutionary platform that make easier to travel agencies and final users to reserve cruises across dozen companies like tibba, wernu, hpv, dgb, etc..We are a “start up”, with a young team of developers and we want to transmit it.. For it, we want something different, a modern business card that represent cruises and technology.. When someone receive this card, this person should say: wowww this is different… this is modern… this is a cruise related company..
- diferent, modern
- traditions business card

```html
<!DOCTYPE html>
<html lang="en">
<head>
<meta charset="utf-8">
<title>Vendalo — Business Card</title>
<link rel="stylesheet" href="https://fonts.googleapis.com/css2?family=Open+Sans:wght@400;600;700&display=swap">
<style>
  :root {
    --stage: #34363a;
    --card-light: #e4e4e4;
    --card-shade: #d6d6d6;
    --brand-blue: #29a8e1;
    --brand-blue-deep: #1f93c9;
    --ink: #1b1b1b;
    --ink-soft: #3a3a3a;
    --rule: #9a9a9a;
    --white: #ffffff;
  }
  * { box-sizing: border-box; margin: 0; padding: 0; }
  html, body {
    width: 1200px; height: 896px; overflow: hidden;
    background: var(--stage);
    font-family: "Open Sans", sans-serif;
  }
  .stage {
    width: 1200px; height: 896px;
    display: flex; flex-direction: column; align-items: center; justify-content: center;
    gap: 60px;
  }
  .card {
    position: relative;
    width: 640px; height: 366px;
    overflow: hidden;
    box-shadow: 0 10px 30px rgba(0,0,0,.45);
  }

  /* Front side */
  .card-front { background: linear-gradient(135deg, var(--card-light) 0%, var(--card-light) 55%, var(--card-shade) 100%); }
  .card-front .accent-band {
    position: absolute; left: 0; right: 0; bottom: 0; height: 16px;
    background: var(--brand-blue);
  }
  .contact-block { position: absolute; left: 40px; top: 62px; }
  .person-name {
    color: var(--brand-blue); font-weight: 700; font-size: 19px; letter-spacing: .5px;
    text-transform: uppercase; line-height: 1.1;
  }
  .person-role { color: var(--ink-soft); font-size: 15px; margin-bottom: 14px; }
  .contact-line {
    display: flex; align-items: center; gap: 8px;
    color: var(--ink); font-size: 15px; line-height: 1.5;
  }
  .contact-line svg { width: 13px; height: 13px; fill: var(--brand-blue); flex: none; }
  .wordmark-dark {
    position: absolute; right: 46px; top: 120px;
    color: var(--ink); font-weight: 600; font-size: 64px; letter-spacing: 2px;
  }
  .divider {
    position: absolute; left: 40px; right: 40px; top: 236px;
    height: 1px; background: var(--rule);
  }
  .address {
    position: absolute; right: 46px; top: 254px; text-align: right;
    color: var(--ink); font-size: 15px; line-height: 1.45;
  }

  /* Back side */
  .card-back {
    background: linear-gradient(120deg, var(--brand-blue) 0%, var(--brand-blue) 50%, var(--brand-blue-deep) 100%);
  }
  .back-texture {
    position: absolute; inset: 0;
    background: linear-gradient(160deg, rgba(255,255,255,.10) 0%, rgba(255,255,255,0) 45%);
  }
  .wordmark-light {
    position: absolute; left: 0; right: 0; top: 124px; text-align: center;
    color: var(--white); font-weight: 600; font-size: 72px; letter-spacing: 3px;
  }
  .website {
    position: absolute; left: 96px; top: 250px;
    color: var(--white); font-size: 16px; letter-spacing: .3px;
  }
</style>
</head>
<body>
<main class="stage">
  <section class="card card-front" aria-label="Card front">
    <div class="contact-block">
      <p class="person-name">Marcus Delane</p>
      <p class="person-role">Managing Director</p>
      <p class="contact-line">
        <svg viewBox="0 0 16 16" aria-hidden="true"><path d="M3 1h3l1.5 4-2 1.3a9 9 0 0 0 4.2 4.2L11 8.5l4 1.5v3a2 2 0 0 1-2 2A13 13 0 0 1 1 3a2 2 0 0 1 2-2z"/></svg>
        031-482 907 615
      </p>
      <p class="contact-line">
        <svg viewBox="0 0 16 16" aria-hidden="true"><path d="M4.5 0h7A1.5 1.5 0 0 1 13 1.5v13a1.5 1.5 0 0 1-1.5 1.5h-7A1.5 1.5 0 0 1 3 14.5v-13A1.5 1.5 0 0 1 4.5 0zM5 2v10h6V2zm3 11a1 1 0 1 0 0 2 1 1 0 0 0 0-2z"/></svg>
        031-482 907 615
      </p>
      <p class="contact-line">
        <svg viewBox="0 0 16 16" aria-hidden="true"><path d="M0 3h16v10H0zm1.5 1.2v.3L8 9l6.5-4.5v-.3zM1.5 6.3v5.2h13V6.3L8 10.8z"/></svg>
        info@vendalo.com
      </p>
    </div>
    <p class="wordmark-dark">Vendalo</p>
    <div class="divider"></div>
    <p class="address">12345, Address Goes Here<br>Country Name, 123456</p>
    <div class="accent-band"></div>
  </section>

  <section class="card card-back" aria-label="Card back">
    <div class="back-texture"></div>
    <p class="wordmark-light">Vendalo</p>
    <p class="website">www.vendalo.com</p>
  </section>
</main>
</body>
</html>
```